Coaching landingpage/salespage need a layout

Hi!
We are two people from Sweden looking for help to design our coaching landingpage/salespage.

What about:
We need a nice modern timeless appealing Photoshop layout (landingpage) for our coaching page where we coach people to “how to get a richer lifestyle”.

Style of page:
We want the site to reflect seriousness but still harmonic. We would like somewhat colorful and (but not too crazy). After all, we are coaching about investments and private economy.
Responsive layout – consider stacking order when scaling down window width. Fullpage-design where content areas are 960 grid/max-width.

----------------------------------------------------------------------------
Content on page:
*Headersection – Logo and header image with the two coaches together and space for later on adding a video.

*On the landingpage the customers can read up on what we mean by a richer lifestyle (use dummy text). We show our Vardagskompassen (= Lifestyle matrix) and a little description about that. If the customers want to know more, they can click "read more (or a symbolic icon that relates to read more)" to expand a hidden div (section) where they can read more about Vardagskompassen. They can also minimize the section.

*3-4 Unique selling points “Four reasons why choose coaching” with nice designed number-icons and some place for text.

*The customer should also be able to read something about what happens during a typical coaching session, some bullets that summarize it (use dummy text) and a couple of headlines, maybe 3 or 4 (about what they need to prepare for themselves .eg Skype, headset/microphone etc).

*Offer/product section: A section where the customer can see what services we provide, choose product and click order. When customer click order they will arrive to an order-page (this one you don’t have to design) .
Our products are as followed: Bronze (single coaching session), Silver (small-package), Gold (large-package). Use provided graphics for these products.

*Testimonials section. Currently we have 2 good testimonials, but only with text no portrait picture.

Testimonial1: “Uppiggande och inspirerande! Kommer med enkla vardagstips såväl som svårare tips. Ett roligt sätt att få en spark i baken, så att ekonomi-energin bibehålls! Tack för ett bra samtal!" - Helena Brattvik

Testimonial2: "Värdefullast för mig var kunskapen om alternativa investeringssställen som inte är börs eller eget ägande." - Annika Sjöstedt

*Section with portraits and info about the coaches (currently 2 coaches, but in future will be several, so a design-section that’s lets us add more coaches).

*Footer-section
------------------------------------------------------------------------

Colors:
Use Vardagskompassen (attached file) as colorinspiration. Doesn’t have to be exactly those colors, you can use similar colors if it is more pleasing to the eye and you can also use complementary colors.

Currently we have tried of our own but don't really nail it with any apealing design. This is what we have done so far but we want to replace it with your more professional design:

https://www.harborkite.se/full/Page/coaching13
-------------------------------------------------------------

SUMMARIZE of the above design-description:

* Our logo (attached psd-file with smart-object. You can try different colors with color-overlay)

*Apealing headerimage with portrait (attached file "big_portrait")

*Introduction text (use dummy text about 100 words)

*Text about Vardagskompassen (use dummy text about 200 words)

*Vardagskompassen (attached psd-file with smart-object)

*What we are covering during a coaching session (dummy text about 200 words and about 5 or 6 bullets)

*3-4 Unique Selling Points with stylish number icons (not 2 small) and some text.
*Our offers Bronze, Silver, Gold (attached pictures)
*Testimonials
*Picture & info about coaches (attached pictures, choose whichever suits you)
*Footer

Please comment if there are questions.

Target Market(s)

People who want to learn how to create a richer lifestyle which involves more freedom and a better well-being

Number of Pages Required

1 page

Font styles to use
Sans Serif
Other font styles liked:
• Roboto

Requirements
Should not have
• A cheezy unmodern landingpage with lots of texts and 10 sign-up buttons.
• This page is not a site about capturing emails and building lists by provide a "best-guide-for-something". It´s about getting people to book and pay for one or more coaching-sessions.

```html
<!DOCTYPE html>
<html lang="sv">
<head>
<meta charset="utf-8">
<title>Harbor Kite – Coaching</title>
<link rel="stylesheet" href="https://fonts.googleapis.com/css2?family=Open+Sans:ital,wght@0,300;0,400;0,600;0,700;1,400&family=Roboto:wght@300;400;500;700&display=swap">
<style>
:root{
  --navy:#1f4e7d;
  --navy-dark:#173c61;
  --blue:#2c6ba7;
  --ribbon:#29a2dc;
  --ribbon-dark:#1f82b6;
  --ink:#2b2b2b;
  --light:#f3f3f3;
  --grey:#e6e6e6;
  --btn:#2f2f2f;
  --brown:#a27b5c;
  --sky:#2aa3de;
  --orange:#f39a1e;
  --green:#3caf62;
}
*{margin:0;padding:0;box-sizing:border-box}
html,body{width:1200px;height:3659px;overflow:hidden}
body{font-family:"Open Sans",Arial,sans-serif;color:var(--ink);background:#fff;position:relative}
section,header,footer{position:absolute;left:0;width:1200px}
.abs{position:absolute}
.btn{position:absolute;background:var(--btn);color:#fff;font:600 15px "Open Sans",sans-serif;display:flex;align-items:center;justify-content:center;border-radius:2px}
.section-title{position:absolute;left:0;width:1200px;text-align:center;font:400 38px "Roboto",sans-serif;text-transform:uppercase;color:#222;letter-spacing:.5px}
.section-title span{color:var(--blue)}
.title-rule{position:absolute;left:450px;width:300px;height:2px;background:#bbb}
.title-rule::after{content:"";position:absolute;left:144px;top:-4px;width:12px;height:10px;background:#999;border-radius:1px}
.body-text{font-size:13.5px;line-height:22px;color:#333;text-align:center}

/* header */
.site-header{top:0;height:93px;background:#fff;border-bottom:1px solid #ddd}
.brand{left:98px;top:22px;display:flex;align-items:center;gap:14px}
.brand-mark{width:46px;height:46px;background:var(--navy)}
.brand-name{font:400 40px "Roboto",sans-serif;color:var(--navy);letter-spacing:2px;text-transform:uppercase}
.contact-bar{right:98px;top:32px;font:600 22px "Open Sans",sans-serif;color:var(--navy);display:flex;gap:22px;align-items:center}

/* hero */
.hero{top:93px;height:480px}
.hero-photo{position:absolute;inset:0;background:linear-gradient(100deg,#3d3a35 0%,#8a7a63 30%,#c9b99a 55%,#5f5a52 75%,#2d2c2a 100%)}
.hero-shade{position:absolute;inset:0;background:linear-gradient(90deg,rgba(0,0,0,.45),rgba(0,0,0,0) 55%)}
.hero-kicker{left:100px;top:196px;font:400 30px "Roboto",sans-serif;color:#fff}
.hero-title{left:100px;top:234px;font:500 38px "Roboto",sans-serif;color:#fff;text-transform:uppercase}
.hero-cta{left:100px;top:302px;height:34px;padding:0 12px;background:rgba(20,40,70,.85);color:#fff;font:700 14px "Open Sans",sans-serif;display:flex;align-items:center;gap:10px}
.hero-cta i{width:24px;height:24px;border:2px solid #fff;border-radius:50%;display:flex;align-items:center;justify-content:center}
.video{left:664px;top:97px;width:502px;height:298px;border:4px solid #fff;background:#222;box-shadow:0 4px 14px rgba(0,0,0,.4)}
.video-still{position:absolute;left:0;top:0;width:494px;height:250px;background:linear-gradient(180deg,#6f9fd4 0%,#a9c7e6 45%,#4a4a52 100%)}
.video-controls{position:absolute;left:0;bottom:0;width:494px;height:40px;background:#1a1a1a}
.hero-base{top:570px;height:3px;background:var(--navy)}

/* about */
.about{top:573px;height:317px;background:var(--light)}

/* matrix */
.matrix{top:890px;height:518px;background:#fff;border-top:1px solid #ddd}
.matrix-item{position:absolute;top:220px;width:220px;text-align:center}
.matrix-icon{width:84px;height:84px;border-radius:50%;margin:0 auto;display:flex;align-items:center;justify-content:center}
.matrix-label{margin-top:22px;font:600 18px "Open Sans",sans-serif;text-transform:uppercase}
.matrix-desc{margin-top:8px;font-size:12.5px;line-height:17px;color:#333}

/* why */
.why{top:1408px;height:646px;background:linear-gradient(180deg,#fafafa,#ececec);border-top:1px solid #ccc}
.why-strip{left:0;top:0;width:190px;height:646px;background:#d9d9d9;border-right:2px solid #c4c4c4}
.reason{position:absolute;left:98px;width:1004px;height:90px}
.reason svg{position:absolute;left:0;top:0}
.reason p{position:absolute;left:112px;top:12px;width:860px;color:#fff;font-size:12.5px;line-height:21px}

/* products */
.products{top:2054px;height:483px;background:#fff}
.products-band{left:0;top:0;width:1200px;height:227px;background:var(--navy)}
.products .section-title{color:#fff}
.products .title-rule{background:rgba(255,255,255,.5)}
.products .title-rule::after{background:#fff}
.plan{position:absolute;top:123px;width:260px;text-align:center}
.medal{width:184px;height:184px;border-radius:50%;margin:0 auto;border:6px solid #fff;box-shadow:0 4px 10px rgba(0,0,0,.35)}
.plan-name{margin-top:14px;font:600 22px "Open Sans",sans-serif;color:var(--navy);text-transform:uppercase}
.plan-sub{font-size:16px;color:#333;margin-top:2px}
.plan .btn{position:relative;margin:8px auto 0;width:196px;height:36px;font-size:15px}

/* testimonials */
.testimonials{top:2537px;height:371px;background:var(--grey)}
.quote-card{position:absolute;top:135px;width:476px;height:146px;background:#fff;box-shadow:0 2px 5px rgba(0,0,0,.12)}
.quote-card::after{content:"";position:absolute;left:60px;bottom:-16px;border-left:16px solid transparent;border-right:16px solid transparent;border-top:16px solid #fff}
.quote-text{position:absolute;left:46px;top:20px;width:400px;font:italic 400 13px/20px "Open Sans",sans-serif;color:#333}
.quote-mark{position:absolute;left:14px;top:14px;font:700 40px Georgia,serif;color:#bbb;line-height:1}
.quote-by{position:absolute;left:0;top:104px;width:100%;text-align:center;font-size:13px}
.quote-by b{font-weight:700;margin-right:8px}
.quote-by span{border-left:1px solid #999;padding-left:8px;color:#444}
.quote-badge{position:absolute;top:290px;width:62px;height:62px;border-radius:50%;background:#9a9a9a;color:#fff;display:flex;align-items:center;justify-content:center;font:700 38px Georgia,serif}

/* coaches */
.coaches{top:2908px;height:495px;background:#fff}
.coach{position:absolute;top:172px;height:276px;background:#fff;border:1px solid #cfd8e3;box-shadow:0 1px 4px rgba(0,0,0,.1)}
.coach-photo{position:absolute;left:0;top:0;width:250px;height:276px;background:var(--navy)}
.coach-photo .shot{position:absolute;left:8px;top:8px;width:234px;height:220px;background:linear-gradient(180deg,#8fa9c1,#5a6f85)}
.coach-name{position:absolute;left:0;bottom:0;width:250px;height:46px;color:#fff;font:600 18px "Open Sans",sans-serif;display:flex;align-items:center;justify-content:center}
.coach-bio{position:absolute;left:264px;top:18px;width:186px;font-size:12.5px;line-height:21px;color:#333;text-align:justify;letter-spacing:.2px}

/* footer */
.site-footer{top:3403px;height:256px;background:var(--navy);color:#fff}
.footer-col h4{font:600 16px "Open Sans",sans-serif;margin-bottom:14px}
.footer-col li{list-style:none;font-size:12.5px;margin-bottom:22px}
.footer-col li::before{content:"›";margin-right:10px;font-weight:700}
.contact-row{display:flex;gap:10px;font-size:12.5px;line-height:17px;margin-bottom:14px;align-items:flex-start}
.map{left:559px;top:74px;width:266px;height:110px;background:linear-gradient(135deg,#e9e6df,#cfd6c9);border:2px solid #fff}
.footer-divider{left:862px;top:20px;width:1px;height:180px;background:rgba(255,255,255,.3)}
.footer-brand{left:880px;top:96px;width:300px;text-align:center}
.footer-brand .brand-name{color:#fff;font-size:30px}
.footer-brand .brand-mark{width:40px;height:40px;background:#fff;margin:0 auto 10px}
.copyright{left:0;top:212px;width:1200px;height:44px;background:var(--navy-dark);font-size:12.5px;display:flex;align-items:center;padding:0 98px;justify-content:space-between}
.social-dot{width:22px;height:22px;border-radius:50%;background:#fff}
</style>
</head>
<body>

<header class="site-header">
  <div class="abs brand"><div class="brand-mark"></div><div class="brand-name">Harbor Kite</div></div>
  <div class="abs contact-bar">
    <span>@ team@harborkite.se</span>
    <span style="display:flex;align-items:center;gap:8px">
      <svg width="20" height="20" viewBox="0 0 20 20"><circle cx="10" cy="10" r="9" fill="none" stroke="#1f4e7d" stroke-width="2"/><path d="M7 5l2 3-1.3 1.2c.7 1.4 1.7 2.4 3.1 3.1L12 11l3 2-1 2c-4 0-8-4-8-8z" fill="#1f4e7d"/></svg>
      123-555-0190</span>
  </div>
</header>

<section class="hero">
  <div class="hero-photo" role="img" aria-label="Header photo: stone villa with luxury cars in the driveway at sunset"></div>
  <div class="hero-shade"></div>
  <div class="abs hero-kicker">Step By Step To</div>
  <div class="abs hero-title">A Richer Lifestyle</div>
  <div class="abs hero-cta">WATCH OUR VIDEO <i><svg width="10" height="10" viewBox="0 0 10 10"><path d="M2 1l7 4-7 4z" fill="#fff"/></svg></i></div>
  <div class="abs video">
    <div class="video-still" role="img" aria-label="Video still: the two coaches standing together under a blue sky"></div>
    <div class="video-controls">
      <svg width="494" height="40" viewBox="0 0 494 40">
        <rect x="10" y="18" width="290" height="4" rx="2" fill="#555"/>
        <rect x="10" y="18" width="170" height="4" rx="2" fill="#d22"/>
        <circle cx="180" cy="20" r="6" fill="#eee"/>
        <rect x="320" y="14" width="14" height="12" fill="#ccc"/>
        <rect x="345" y="14" width="14" height="12" fill="#ccc"/>
        <text x="372" y="25" fill="#ccc" font-size="11" font-family="Open Sans, sans-serif">HD ON</text>
        <rect x="420" y="18" width="40" height="4" rx="2" fill="#777"/>
        <circle cx="470" cy="20" r="8" fill="#eee"/>
      </svg>
    </div>
  </div>
</section>
<div class="abs hero-base" style="left:0;width:1200px"></div>

<section class="about">
  <h2 class="section-title" style="top:48px">About <span>Harbor Kite</span></h2>
  <div class="title-rule" style="top:104px"></div>
  <p class="abs body-text" style="left:112px;top:118px;width:976px">Lorem ipsum dolor sit amet, consectetuer adipiscing elit, sed diam nonummy nibh euismod tincidunt ut laoreet dolore magna aliquam erat volutpat. Ut wisi enim ad minim veniam, quis nostrud exerci tation ullamcorper suscipit lobortis nisl ut aliquip ex ea commodo consequat. Duis autem vel eum iriure dolor in hendrerit in vulputate velit esse molestie consequat, vel illum dolore eu feugiat nulla facilisis at vero eros et accumsan et iusto odio dignissim qui blandit praesent luptatum zzril delenit augue duis dolore te feugait nulla facilisi.</p>
  <div class="btn" style="left:540px;top:236px;width:120px;height:28px;font-size:12px">Read More »</div>
</section>

<section class="matrix">
  <h2 class="section-title" style="top:46px">Our <span>Lifestyle Matrix</span></h2>
  <div class="title-rule" style="top:102px"></div>
  <p class="abs body-text" style="left:110px;top:118px;width:980px;font-weight:600;font-size:13px">What is a richer lifestyle may differ between different people. It can also be quite difficult on their own to get a good picture of what you really mean by this. We have therefore developed a simple model to facilitate the understanding and the creation of a richer lifestyle. This is a model we call lifestyle matrix and consists of the following four parts representing respective lifestyle.</p>

  <div class="matrix-item" style="left:141px">
    <div class="matrix-icon" style="background:var(--brown)"><svg width="40" height="40" viewBox="0 0 40 40"><path d="M20 30s-10-6-10-13a5 5 0 0 1 10-2 5 5 0 0 1 10 2c0 7-10 13-10 13z" fill="#fff"/></svg></div>
    <div class="matrix-label" style="color:var(--brown)">Prosperous</div>
    <div class="matrix-desc">Lorem ipsum dolor sit am et, consectetuer sit ame Lorem ipsum dolor sit am</div>
  </div>
  <div class="matrix-item" style="left:371px">
    <div class="matrix-icon" style="background:var(--sky)"><svg width="40" height="40" viewBox="0 0 40 40"><circle cx="20" cy="20" r="12" fill="none" stroke="#fff" stroke-width="3"/><path d="M20 12v8l6 4" stroke="#fff" stroke-width="3" fill="none"/></svg></div>
    <div class="matrix-label" style="color:var(--sky)">Rat Race</div>
    <div class="matrix-desc">Lorem ipsum dolor sit am et, consectetuer sit ame Lorem ipsum dolor sit am</div>
  </div>
  <div class="matrix-item" style="left:617px">
    <div class="matrix-icon" style="background:var(--orange)"><svg width="40" height="40" viewBox="0 0 40 40"><circle cx="20" cy="16" r="8" fill="#fff"/><path d="M8 30h24v4H8z" fill="#fff"/></svg></div>
    <div class="matrix-label" style="color:var(--orange)">A Richer</div>
    <div class="matrix-desc">Lorem ipsum dolor sit am et, consectetuer sit ame Lorem ipsum dolor sit am</div>
  </div>
  <div class="matrix-item" style="left:844px">
    <div class="matrix-icon" style="background:var(--green)"><svg width="40" height="40" viewBox="0 0 40 40"><path d="M6 22l14-4 14-10-8 16-10 2-4 6z" fill="#fff"/></svg></div>
    <div class="matrix-label" style="color:var(--green)">Freedom</div>
    <div class="matrix-desc">Lorem ipsum dolor sit am et, consectetuer sit ame Lorem ipsum dolor sit am</div>
  </div>

  <div class="btn" style="left:540px;top:433px;width:120px;height:30px;font-size:13px">Get Started »</div>
</section>

<section class="why">
  <div class="abs why-strip"></div>
  <h2 class="section-title" style="top:42px">Why <span>Choose Coaching ?</span></h2>
  <div class="title-rule" style="top:98px;left:455px;width:290px"></div>

  <div class="reason" style="top:136px">
    <svg width="1004" height="90" viewBox="0 0 1004 90"><polygon points="0,45 16,8 96,8 96,82 16,82" fill="var(--ribbon-dark)"/><polygon points="96,0 1004,0 984,45 1004,90 96,90" fill="var(--ribbon)"/><path d="M44 52v-14h5l5-9c3 0 4 2 3 5l-1 4h8c2 0 3 2 2 4l-3 10h-14z" fill="#fff"/></svg>
    <p>Lorem ipsum dolor sit amet, consectetuer adipiscing elit, sed diam nonummy nibh euismod tincidunt ut laoreet dolore magna aliquam erat volutpat. Ut wisi enim ad minim veniam, quis nostrud exerci tation ullamcorper suscipit lobortis nisl ut aliquip ex ea commodo consequat. Duis autem vel eum iriure dolor in hendrerit in vulputate velit esse molestie consequat, vel illum dolore eu feugiat nulla facilisis at vero.</p>
  </div>
  <div class="reason" style="top:246px">
    <svg width="1004" height="90" viewBox="0 0 1004 90"><polygon points="0,45 16,8 96,8 96,82 16,82" fill="var(--ribbon-dark)"/><polygon points="96,0 1004,0 984,45 1004,90 96,90" fill="var(--ribbon)"/><path d="M44 52v-14h5l5-9c3 0 4 2 3 5l-1 4h8c2 0 3 2 2 4l-3 10h-14z" fill="#fff"/></svg>
    <p>Lorem ipsum dolor sit amet, consectetuer adipiscing elit, sed diam nonummy nibh euismod tincidunt ut laoreet dolore magna aliquam erat volutpat. Ut wisi enim ad minim veniam, quis nostrud exerci tation ullamcorper suscipit lobortis nisl ut aliquip ex ea commodo consequat. Duis autem vel eum iriure dolor in hendrerit in vulputate velit esse molestie consequat, vel illum dolore eu feugiat nulla facilisis at vero.</p>
  </div>
  <div class="reason" style="top:366px">
    <svg width="1004" height="90" viewBox="0 0 1004 90"><polygon points="0,45 16,8 96,8 96,82 16,82" fill="var(--ribbon-dark)"/><polygon points="96,0 1004,0 984,45 1004,90 96,90" fill="var(--ribbon)"/><path d="M44 52v-14h5l5-9c3 0 4 2 3 5l-1 4h8c2 0 3 2 2 4l-3 10h-14z" fill="#fff"/></svg>
    <p>Lorem ipsum dolor sit amet, consectetuer adipiscing elit, sed diam nonummy nibh euismod tincidunt ut laoreet dolore magna aliquam erat volutpat. Ut wisi enim ad minim veniam, quis nostrud exerci tation ullamcorper suscipit lobortis nisl ut aliquip ex ea commodo consequat. Duis autem vel eum iriure dolor in hendrerit in vulputate velit esse molestie consequat, vel illum dolore eu feugiat nulla facilisis at vero.</p>
  </div>
  <div class="reason" style="top:485px">
    <svg width="1004" height="90" viewBox="0 0 1004 90"><polygon points="0,45 16,8 96,8 96,82 16,82" fill="var(--ribbon-dark)"/><polygon points="96,0 1004,0 984,45 1004,90 96,90" fill="var(--ribbon)"/><path d="M44 52v-14h5l5-9c3 0 4 2 3 5l-1 4h8c2 0 3 2 2 4l-3 10h-14z" fill="#fff"/></svg>
    <p>Lorem ipsum dolor sit amet, consectetuer adipiscing elit, sed diam nonummy nibh euismod tincidunt ut laoreet dolore magna aliquam erat volutpat. Ut wisi enim ad minim veniam, quis nostrud exerci tation ullamcorper suscipit lobortis nisl ut aliquip ex ea commodo consequat. Duis autem vel eum iriure dolor in hendrerit in vulputate velit esse molestie consequat, vel illum dolore eu feugiat nulla facilisis at vero.</p>
  </div>
</section>

<section class="products">
  <div class="abs products-band"></div>
  <h2 class="section-title" style="top:36px">Our Products</h2>
  <div class="title-rule" style="top:92px"></div>
  <div class="plan" style="left:138px">
    <div class="medal" role="img" aria-label="Bronze product medal" style="background:radial-gradient(circle at 40% 35%,#f0a56a,#c9702f 60%,#9a4f1c)"></div>
    <div class="plan-name">Bronze</div>
    <div class="plan-sub">single coaching session</div>
    <div class="btn">Make An Appointment</div>
  </div>
  <div class="plan" style="left:470px">
    <div class="medal" role="img" aria-label="Gold product medal" style="background:radial-gradient(circle at 40% 35%,#fbe27a,#e5b424 60%,#b88a0e)"></div>
    <div class="plan-name">Gold</div>
    <div class="plan-sub">large-package</div>
    <div class="btn">Make An Appointment</div>
  </div>
  <div class="plan" style="left:802px">
    <div class="medal" role="img" aria-label="Silver product medal" style="background:radial-gradient(circle at 40% 35%,#f4f4f4,#c8c8c8 60%,#9a9a9a)"></div>
    <div class="plan-name">Silver</div>
    <div class="plan-sub">small-package</div>
    <div class="btn">Make An Appointment</div>
  </div>
</section>

<section class="testimonials">
  <h2 class="section-title" style="top:46px">Clients <span>Testimonials</span></h2>
  <div class="title-rule" style="top:102px"></div>
  <div class="quote-card" style="left:115px">
    <div class="quote-mark">“</div>
    <p class="quote-text">Uppiggande och inspirerande! Kommer med enkla vardagstips såväl som svårare tips. Ett roligt sätt att få en spark i baken, så att ekonomi-energin bibehålls! Tack för ett bra samtal!</p>
    <div class="quote-by"><b>Helena Brattvik</b><span>Customer</span></div>
  </div>
  <div class="quote-badge" style="left:130px">“</div>
  <div class="quote-card" style="left:637px">
    <div class="quote-mark">“</div>
    <p class="quote-text">Värdefullast för mig var kunskapen om alternativa investeringssställen som inte är börs eller eget ägande.</p>
    <div class="quote-by"><b>Annika Sjöstedt</b><span>Customer</span></div>
  </div>
  <div class="quote-badge" style="left:652px">“</div>
</section>

<section class="coaches">
  <h2 class="section-title" style="top:60px">Our <span>Coaches</span></h2>
  <div class="title-rule" style="top:116px"></div>
  <article class="coach" style="left:98px;width:464px">
    <div class="coach-photo"><div class="shot" role="img" aria-label="Portrait photo of coach Joakim Ekström"></div><div class="coach-name">Joakim Ekström</div></div>
    <p class="coach-bio">Fredrik har en bred bakgrund inom ekonomi och IT. Som investerare ligger hans fokus på utdelningsaktier, fastigheter och internetbaserat entreprenörskap. Han har också en lång erfarenhet och en stor passion av att hjälpa människor...[+]</p>
  </article>
  <article class="coach" style="left:620px;width:483px">
    <div class="coach-photo"><div class="shot" role="img" aria-label="Portrait photo of coach Fredrik Lindqvist"></div><div class="coach-name">Fredrik Lindqvist</div></div>
    <p class="coach-bio" style="width:200px">Mångsidig investerare med fokus på alternativa och högriskinvesteringar. Förutom börsen, investerar Joakim i onoterade startup-bolag och olika internetbaserade investeringar såsom P2P-lending, onlinespel och appar....[+]</p>
  </article>
</section>

<footer class="site-footer">
  <div class="abs footer-col" style="left:98px;top:36px">
    <h4>Quick Links</h4>
    <ul><li>Blog</li><li>Coaching</li><li>About Us</li></ul>
  </div>
  <div class="abs footer-col" style="left:271px;top:36px;width:260px">
    <h4>Contact Detail</h4>
    <div class="contact-row"><svg width="14" height="18" viewBox="0 0 14 18"><path d="M7 0a7 7 0 0 1 7 7c0 5-7 11-7 11S0 12 0 7a7 7 0 0 1 7-7z" fill="#fff"/><circle cx="7" cy="7" r="2.5" fill="#1f4e7d"/></svg><span><b>Harbor Kite</b><br>Ekbacksgatan 12, 411 05 Göteborg</span></div>
    <div class="contact-row"><svg width="14" height="14" viewBox="0 0 14 14"><path d="M3 0l3 4-2 2c1 2 2 3 4 4l2-2 4 3-2 3C6 14 0 8 0 2z" fill="#fff"/></svg><span>(0123) 555-0142</span></div>
    <div class="contact-row"><svg width="14" height="12" viewBox="0 0 14 12"><rect width="14" height="12" fill="#fff"/><path d="M0 0l7 6 7-6" stroke="#1f4e7d" fill="none"/></svg><span>team@harborkite.se</span></div>
  </div>
  <div class="abs footer-col" style="left:559px;top:36px"><h4>Map</h4></div>
  <div class="abs map" role="img" aria-label="Street map showing the office location"></div>
  <div class="abs footer-divider"></div>
  <div class="abs footer-brand"><div class="brand-mark"></div><div class="brand-name">Harbor Kite</div></div>
  <div class="abs copyright"><span>© 2016 Harbor Kite. All Rights Reserved</span><span class="social-dot"></span></div>
</footer>

</body>
</html>
```